WP website design Pellow - Brantz (Contest)

We need a wordpress design that will incorporate a professional color scheme with company logo in a clean layout. The design needs to consider that this will be developed on a responsive theme. Colors are red and black of the logo and and an accent color. Client wants a 'modern' look.

Industry/Entity Type

It Company

Font styles to use
Serif
Sans Serif

Colors

Designer to choose colors to be used in the design.

Requirements
Must have
• Must Have:
- Navigation: 1) Home; 2) Auctions; 3) Real Estate Listings 4) Assets For Sale 5) Services 6) About Us 7) Contact Us

Site will have slideshow - image is attached. Colors will be those in the logo, red and black with maybe an accent color. A site the client mentions liking is Mubrelbids.com for the use of color and layout.

Widgets: Featured Auctions, 2) Email signup form; 3) Testimonials blog widget; 5) Featured Video; Footer will have affiliation logo and contact info.

Home page content:
We are a family owned and operated business with over 25 years of real estate experience in Clinton and surrounding areas in Western Oklahoma. We know that purchasing a home is one of the most important decisions a person can make, and we strive to make it a successful and enjoyable experience for you!
Enjoy our website and please call if you have any questions or would like to make an appointment to view property!
Also, take a moment to look at our Auction Calendar for upcoming auction dates. Auctions are a great opportunity for great deals and rare finds, not to mention A LOT OF FUN!!

Widgets: 1) Featured Properties; 2) Call to action for Sellers 3) Testimonials blog/widget
Nice to have
• use of dropdown menus

```html
<!DOCTYPE html>
<html lang="en">
<head>
<meta charset="utf-8">
<title>Pellow Auction &amp; Real Estate</title>
<link href="https://fonts.googleapis.com/css2?family=Arimo:ital,wght@0,400;0,700;1,400&family=Cinzel:wght@400&family=Libre+Baskerville:wght@400;700&family=Tinos&display=swap" rel="stylesheet">
<style>
:root{
  --red:#c0152a;
  --red-dark:#9c0f20;
  --ink:#222;
  --text:#333;
  --muted:#555;
  --band:#c8c8c8;
  --panel:#e8e8e8;
  --lower:#e1e1e1;
  --footer:#3a3a3a;
  --footer-base:#1f1f1f;
  --white:#fff;
}
*{box-sizing:border-box;margin:0;padding:0}
html,body{width:831px;height:1200px;overflow:hidden;background:var(--white)}
body{position:relative;font-family:"Arimo",Arial,sans-serif;color:var(--text)}
.abs{position:absolute}

/* header */
.brand{left:74px;top:38px;display:flex;align-items:center;gap:10px}
.brand-mark{width:18px;height:18px;background:var(--red)}
.brand-name{font-family:"Arimo",Arial,sans-serif;font-weight:700;font-size:20px;color:var(--ink);line-height:1}
.follow{left:576px;top:41px;font-size:15px;color:var(--ink);letter-spacing:.5px}
.social{top:38px;width:25px;height:25px;border-radius:50%;background:#555}
.header-rule{left:0;top:95px;width:831px;height:2px;background:var(--ink)}

/* nav */
.nav{left:0;top:97px;width:831px;height:27px;display:flex;align-items:center;padding-left:64px}
.nav a{font-family:"Tinos","Times New Roman",serif;font-size:9.8px;color:var(--ink);text-decoration:none;letter-spacing:.3px;padding:0 13px;border-right:1px solid #bbb;line-height:17px}
.nav a:last-child{border-right:none}
.nav a.active{position:relative}
.nav a.active::after{content:"";position:absolute;left:50%;bottom:-7px;margin-left:-4px;border:4px solid transparent;border-top-color:var(--ink)}

/* hero */
.hero-band{left:0;top:124px;width:831px;height:322px;background:var(--band)}
.hero-frame{left:69px;top:143px;width:693px;height:283px;background:var(--white);padding:3px}
.hero-photo{width:100%;height:100%;background:linear-gradient(180deg,#5d7a4a 0%,#8a4a3a 45%,#9c5444 62%,#5e8a3e 100%)}
.hero-caption{left:246px;top:330px;width:329px;height:34px;background:rgba(192,21,42,.9);color:var(--white);font-family:"Tinos","Times New Roman",serif;font-size:17.5px;text-align:center;line-height:34px;letter-spacing:.3px}
.dropdown{left:110px;top:130px;width:144px;height:73px;background:rgba(235,235,235,.92);padding:8px 7px}
.dropdown a{display:block;height:20px;border-radius:3px;font-size:8.5px;color:var(--white);text-decoration:none;line-height:20px;padding-left:9px;margin-bottom:7px}
.dropdown a::before{content:"";display:inline-block;border:3px solid transparent;border-left:3px solid var(--white);margin-right:3px}
.dd-red{background:var(--red)}
.dd-dark{background:#3d3d3d}

/* welcome */
.welcome-title{left:0;top:467px;width:831px;text-align:center;font-family:"Cinzel",Georgia,serif;font-size:18px;color:var(--ink);letter-spacing:.5px}
.welcome-title span{color:var(--red)}
.welcome-text{left:69px;top:501px;width:693px;text-align:center;font-size:9px;line-height:14px;color:var(--text)}
.divider{left:69px;top:565px;width:693px;height:1px;background:#ddd}

/* featured auctions */
.card{top:597px;width:339px;height:166px;background:var(--panel);border-radius:6px;border:1px solid #ddd}
.card-title{position:absolute;left:11px;top:7px;font-family:"Libre Baskerville",Georgia,serif;font-size:16.5px;color:var(--red)}
.card-sub{position:absolute;left:12px;top:37px;font-family:"Tinos","Times New Roman",serif;font-size:11px;color:var(--ink);letter-spacing:.3px}
.card-photo{position:absolute;left:12px;top:62px;width:134px;height:60px;background:linear-gradient(180deg,#9bb8d6 0%,#a9806a 55%,#6d8f45 100%)}
.btn{position:absolute;top:128px;height:21px;font-size:9.5px;font-weight:700;color:var(--white);line-height:21px;padding-left:20px;border:1px solid #111;box-shadow:0 0 0 1px #fff inset}
.btn-details{left:12px;width:64px;background:#333}
.btn-gallery{left:84px;width:64px;background:var(--red);border-color:var(--red-dark)}
.btn svg{position:absolute;left:7px;top:6px}
.card-info{position:absolute;left:161px;top:64px;width:175px;font-size:8.3px;line-height:14px;font-style:italic;color:var(--ink)}
.card-info h4{font-style:normal;font-size:9.5px;letter-spacing:.5px;margin-bottom:3px}
.card-info b{color:var(--red);font-weight:400}
.card-info p{margin-bottom:4px}

/* lower widgets */
.lower{left:0;top:822px;width:831px;height:232px;background:var(--lower)}
.w-title{top:864px;font-family:"Libre Baskerville",Georgia,serif;font-weight:700;font-size:16.5px;color:var(--red)}
.w-text{font-size:8.5px;line-height:12px;color:var(--ink)}
.field{left:70px;width:170px;height:20px;background:var(--white);border:1px solid #ccc;font-size:9px;color:#888;padding-left:6px;line-height:18px}
.subscribe{left:70px;top:1007px;width:93px;height:23px;border:2px solid #444;border-radius:12px;background:linear-gradient(#fff,#e6e6e6);font-size:9px;font-weight:700;text-align:center;line-height:19px;color:var(--ink);letter-spacing:.4px}
.vline{top:866px;width:1px;height:164px;background:#c4c4c4}
.date{left:288px;width:41px;height:47px;background:var(--white);border-radius:5px;border:1px solid #d6d6d6;text-align:center;color:var(--ink)}
.date strong{display:block;font-size:17px;margin-top:6px}
.date span{font-size:10px}
.prop{left:342px;width:190px;font-size:9px;line-height:14px;color:var(--muted)}
.prop h5{font-weight:400;font-size:10px;color:var(--red);margin-bottom:1px}
.prop i{color:var(--red);font-size:8.5px;margin-left:18px}
.quote{left:557px;top:893px;width:205px;height:122px;background:var(--white);border:1px solid #999;border-radius:4px;padding:15px 8px 0 20px;font-size:8.5px;line-height:13px;color:var(--ink)}
.quote .q{position:absolute;font-family:Georgia,serif;font-size:20px;font-weight:700}
.quote-tail{left:719px;top:1013px}
.avatar{left:651px;top:1020px;width:28px;height:28px;border-radius:50%;background:#c9b6a4;border:2px solid var(--white)}
.author{left:686px;top:1029px;font-size:9.5px;color:var(--red)}

/* footer */
.footer{left:0;top:1054px;width:831px;height:118px;background:var(--footer)}
.badge{top:1091px;height:31px;background:#e9e9e9}
.badge.round{border-radius:50%;width:32px}
.footer-links{left:0;top:1138px;width:831px;display:flex;justify-content:center;font-size:9.5px;color:var(--white)}
.footer-links span{padding:0 13px}
.footer-links span.sep{padding:0}
.base{left:0;top:1172px;width:831px;height:28px;background:var(--footer-base);color:var(--white);font-size:8.5px;text-align:center;line-height:28px}
</style>
</head>
<body>

<header>
  <div class="abs brand">
    <span class="brand-mark" aria-hidden="true"></span>
    <span class="brand-name">Pellow Auction &amp; Real Estate</span>
  </div>
  <div class="abs follow">Follow Us:</div>
  <span class="abs social" style="left:663px" aria-label="Social link 1"></span>
  <span class="abs social" style="left:696px" aria-label="Social link 2"></span>
  <span class="abs social" style="left:730px" aria-label="Social link 3"></span>
  <div class="abs header-rule"></div>
</header>

<nav class="abs nav">
  <a href="#">HOME</a>
  <a href="#" class="active">AUCTIONS</a>
  <a href="#">REAL ESTATE LISTINGS</a>
  <a href="#">ASSETS FOR SALE</a>
  <a href="#">SERVICES</a>
  <a href="#">ABOUT US</a>
  <a href="#">CONTACT US</a>
</nav>

<section>
  <div class="abs hero-band"></div>
  <div class="abs hero-frame"><div class="hero-photo" role="img" aria-label="Slideshow photo of a red brick two-storey house with a green lawn and trees"></div></div>
  <div class="abs hero-caption">PELLOW AUCTION &amp; REAL ESTATE</div>
  <div class="abs dropdown">
    <a href="#" class="dd-red">Referrals</a>
    <a href="#" class="dd-dark">Properties For Sale</a>
  </div>
</section>

<section>
  <h1 class="abs welcome-title" style="font-weight:400"><span>WELCOME TO</span> PELLOW AUCTIONS</h1>
  <p class="abs welcome-text">Lorem ipsum dolor sit amet, consectetur adipisicing elit, sed do eiusmod tempor incididunt ut labore et dolore magna aliqua. Ut enim ad minim veniam, quis nostrud exercitation ullamco laboris nisi ut aliquip ex ea commodo consequat. Duis aute irure dolor in reprehenderit in voluptate velit esse cillum dolore eu fugiat nulla pariatur. Excepteur sint occaecat cupidatat non proident, sunt in culpa qui officia deserunt mollit anim id est laborum...</p>
  <div class="abs divider"></div>
</section>

<section>
  <article class="abs card" style="left:68px">
    <h2 class="card-title" style="font-weight:400">Featured Auctions</h2>
    <div class="card-sub">SHOP EQUIPMENT/TOOLS * PORK PROCESSING ITEMS</div>
    <div class="card-photo" role="img" aria-label="Photo of a stone and brick family house"></div>
    <span class="btn btn-details"><svg width="9" height="9"><circle cx="4.5" cy="4.5" r="4.5" fill="#fff"/><circle cx="2.5" cy="4.5" r=".8" fill="#333"/><circle cx="4.5" cy="4.5" r=".8" fill="#333"/><circle cx="6.5" cy="4.5" r=".8" fill="#333"/></svg>Details</span>
    <span class="btn btn-gallery"><svg width="10" height="9"><rect x=".5" y="1.5" width="9" height="7" fill="none" stroke="#fff"/><circle cx="5" cy="5" r="1.8" fill="#fff"/></svg>Gallery</span>
    <div class="card-info">
      <h4>LIVE ON-SITE AUCTION</h4>
      <p><b>Begins:</b> &nbsp;Tuesday, April 23, 2013</p>
      <p><b>Location:</b> &nbsp;Cedar Ridge Entrance- 1400 N. Prairie Hwy 9 &nbsp;text of the printing and type-setting industry. Lorem Ipsum &nbsp;text of the printing and typesettinghas been &nbsp;text of the</p>
    </div>
  </article>
  <article class="abs card" style="left:422px">
    <h2 class="card-title" style="font-weight:400">Featured Auctions</h2>
    <div class="card-sub">SHOP EQUIPMENT/TOOLS * PORK PROCESSING ITEMS</div>
    <div class="card-photo" role="img" aria-label="Photo of a stone and brick family house"></div>
    <span class="btn btn-details"><svg width="9" height="9"><circle cx="4.5" cy="4.5" r="4.5" fill="#fff"/><circle cx="2.5" cy="4.5" r=".8" fill="#333"/><circle cx="4.5" cy="4.5" r=".8" fill="#333"/><circle cx="6.5" cy="4.5" r=".8" fill="#333"/></svg>Details</span>
    <span class="btn btn-gallery"><svg width="10" height="9"><rect x=".5" y="1.5" width="9" height="7" fill="none" stroke="#fff"/><circle cx="5" cy="5" r="1.8" fill="#fff"/></svg>Gallery</span>
    <div class="card-info">
      <h4>LIVE ON-SITE AUCTION</h4>
      <p><b>Begins:</b> &nbsp;Tuesday, April 23, 2013</p>
      <p><b>Location:</b> &nbsp;Cedar Ridge Entrance- 1400 N. Prairie Hwy 9 &nbsp;text of the printing and type-setting industry. Lorem Ipsum &nbsp;text of the printing and typesettinghas been &nbsp;text of the</p>
    </div>
  </article>
</section>

<section>
  <div class="abs lower"></div>

  <h3 class="abs w-title" style="left:70px">Email Sign Up</h3>
  <p class="abs w-text" style="left:70px;top:902px;width:178px;text-align:justify">Lorem ipsum dolor sit amet, consectetuer adipiscing elit. Nam</p>
  <div class="abs field" style="top:936px">Your Name</div>
  <div class="abs field" style="top:972px">Email Address</div>
  <div class="abs subscribe">Subscribe Now</div>

  <div class="abs vline" style="left:266px"></div>

  <h3 class="abs w-title" style="left:296px">Featured Properties</h3>
  <div class="abs date" style="top:903px"><strong>25</strong><span>Dec</span></div>
  <div class="abs prop" style="top:905px"><h5>Lorem ipsum dolor sit amet</h5>Lorem ipsum dolor sit amet, consectetur adipiscing elit labore aliqua. <i>Read More...</i></div>
  <div class="abs date" style="top:972px"><strong>25</strong><span>Dec</span></div>
  <div class="abs prop" style="top:974px"><h5>Lorem ipsum dolor sit amet</h5>Lorem ipsum dolor sit amet, consectetur adipiscing elit labore aliqua. <i>Read More...</i></div>

  <div class="abs vline" style="left:544px"></div>

  <h3 class="abs w-title" style="left:564px">Client Testimonial</h3>
  <div class="abs quote">
    <span class="q" style="left:9px;top:6px">&#8220;</span>
    <p>Lorem ipsum dolor sit amet, consectetur labore et aliquip ex ea commodo consequat. Duis aute irure dolor in reprehenderit in voluptate.</p>
    <p style="margin-top:13px">velit esse cillum dolore eu fugiat nulla pariatur. anim id est laborum.</p>
    <span class="q" style="left:105px;top:98px">&#8221;</span>
  </div>
  <svg class="abs quote-tail" width="16" height="12" aria-hidden="true"><path d="M0 1 L12 11 L10 1" fill="#fff" stroke="#999"/><rect x="1" y="0" width="9" height="2" fill="#fff"/></svg>
  <div class="abs avatar" role="img" aria-label="Client portrait"></div>
  <div class="abs author">Mr John Smith...</div>
</section>

<footer>
  <div class="abs footer"></div>
  <div class="abs badge" style="left:211px;width:54px" aria-label="Affiliation badge"></div>
  <div class="abs badge" style="left:277px;width:29px" aria-label="Affiliation badge"></div>
  <div class="abs badge round" style="left:317px" aria-label="Affiliation badge"></div>
  <div class="abs badge round" style="left:357px" aria-label="Affiliation badge"></div>
  <div class="abs badge" style="left:396px;width:54px" aria-label="Affiliation badge"></div>
  <div class="abs badge" style="left:460px;width:48px;height:24px;top:1094px" aria-label="Affiliation badge"></div>
  <div class="abs badge" style="left:514px;width:94px;height:28px;top:1093px" aria-label="Affiliation badge"></div>
  <nav class="abs footer-links">
    <span>Home</span><span class="sep">|</span><span>Auctions</span><span class="sep">|</span><span>For Sale</span><span class="sep">|</span><span>Buyers &amp; Sellers</span><span class="sep">|</span><span>Brokerage</span><span class="sep">|</span><span>About Us</span><span class="sep">|</span><span>Contact Us</span>
  </nav>
  <div class="abs base">Copyright (C) pellow auction and real estate. &nbsp;All Rights Reserved</div>
</footer>

</body>
</html>
```